business card design for a plumbing contractor

i need a double business card for a plumbing business, our initial service is residential Sewer Drain Cleaning.

Target Market(s)

other plumbing Business

Industry/Entity Type

Plumbing

Contact Information for Business Card

www.PipeworksTopMark.example- 5307218394-

Font styles to use
Serif

Colors
ec1f27
0455a3

```html
<!DOCTYPE html>
<html lang="en">
<head>
<meta charset="utf-8">
<title>Pipeworks Top Mark – Business Card</title>
<link rel="stylesheet" href="https://fonts.googleapis.com/css2?family=Roboto+Condensed:wght@400;700&display=swap">
<style>
  :root{
    --stage:#e9e6e1;
    --card-white:#f7f7f6;
    --brand-red:#d9332c;
    --ink-grey:#7d7a72;
    --ink-dark:#4a4a48;
    --paper-white:#ffffff;
  }
  *{box-sizing:border-box;margin:0;padding:0}
  html,body{width:1200px;height:886px;overflow:hidden}
  body{
    background:var(--stage);
    font-family:"Roboto Condensed",Arial,sans-serif;
    display:flex;align-items:center;justify-content:center;gap:40px;
  }
  .card{
    position:relative;width:540px;height:310px;border-radius:18px;overflow:hidden;
    box-shadow:0 8px 24px rgba(0,0,0,.18);
  }
  /* front */
  .card-front{background:var(--card-white)}
  .corner-tab{position:absolute;top:0;right:0;width:64px;height:14px;background:var(--brand-red)}
  .holder{position:absolute;top:34px;right:30px;text-align:right}
  .holder-name{color:var(--brand-red);font-weight:700;font-size:21px;letter-spacing:.3px}
  .holder-role{color:var(--ink-grey);font-size:15px;margin-top:2px}
  .wordmark{
    position:absolute;left:40px;top:150px;display:flex;align-items:center;gap:10px;
    color:var(--ink-grey);font-weight:700;font-size:30px;line-height:1;
  }
  .wordmark-dot{width:16px;height:16px;background:var(--brand-red)}
  .contact{position:absolute;left:40px;bottom:30px;list-style:none;color:var(--ink-dark);font-size:14px}
  .contact li{display:flex;align-items:center;gap:8px;margin-top:4px}
  .contact svg{width:12px;height:12px;flex:none}
  .contact .web{letter-spacing:1px;padding-left:20px}
  /* back */
  .card-back{background:var(--brand-red);color:var(--paper-white)}
  .back-brand{position:absolute;right:34px;bottom:110px;font-weight:700;font-size:38px;line-height:1}
  .services{position:absolute;right:34px;bottom:26px;list-style:none;text-align:right;font-size:15px;line-height:1.4}
  .services li::after{content:" •";font-weight:700}
</style>
</head>
<body>
  <section class="card card-front" aria-label="Business card front">
    <div class="corner-tab"></div>
    <div class="holder">
      <p class="holder-name">DANA WHITFIELD</p>
      <p class="holder-role">CEO/FOUNDER</p>
    </div>
    <div class="wordmark"><span>Pipeworks Top Mark</span><span class="wordmark-dot"></span></div>
    <ul class="contact">
      <li>
        <svg viewBox="0 0 12 12" aria-hidden="true"><path d="M3 1 L5 3.5 L4 5 Q5.5 7.5 7 8 L8.5 7 L11 9 L9.5 11 Q4 10.5 1 3 Z" fill="var(--brand-red)"/></svg>
        5307218394
      </li>
      <li>
        <svg viewBox="0 0 12 12" aria-hidden="true"><rect x="0.5" y="2" width="11" height="8" fill="var(--brand-red)"/><path d="M1 2.5 L6 6.5 L11 2.5" stroke="#fff" fill="none"/></svg>
        Dispatch@PipeworksTopMark.example
      </li>
      <li class="web">www.PipeworksTopMark.example</li>
    </ul>
  </section>

  <section class="card card-back" aria-label="Business card back">
    <p class="back-brand">Pipeworks Top Mark</p>
    <ul class="services">
      <li>Sewer Drain Cleaning</li>
      <li>Maintenance</li>
      <li>Trenchless Pipe Installs</li>
    </ul>
  </section>
</body>
</html>
```